TernVAX Business Cards

Create business cards for our exciting new software company. We provide cloud billing systems and provisioning software for campany that need monthly SaaS and Cloud Billing

Target Market(s)

Enterprise businesses, b2b, telecom carriers, software manufactures

Industry/Entity Type

Software

```html
<!DOCTYPE html>
<html lang="en">
<head>
<meta charset="utf-8">
<title>TernVAX Business Cards</title>
<link rel="stylesheet" href="https://fonts.googleapis.com/css2?family=Lato:wght@300;400;700&display=swap">
<style>
  :root {
    --page-bg: #e6eaed;
    --card-white: #ffffff;
    --navy: #1b3a5c;
    --navy-deep: #173553;
    --sky: #5fa9cc;
    --blue-dark: #1e4667;
    --blue-mid: #3d7199;
    --blue-light: #6aa3c6;
    --text-grey: #6d6f72;
    --tagline-grey: #7c8186;
    --tagline-light: #dbe8f1;
  }
  * { box-sizing: border-box; margin: 0; padding: 0; }
  html, body { width: 1200px; height: 960px; overflow: hidden; }
  body {
    background: var(--page-bg);
    font-family: "Lato", Arial, sans-serif;
    position: relative;
  }
  .card {
    position: absolute;
    left: 250px;
    width: 700px;
    height: 400px;
    box-shadow: 0 10px 30px rgba(30, 50, 70, 0.18);
    overflow: hidden;
  }
  /* Front card */
  .card-front { top: 60px; background: var(--card-white); }
  .front-brand { position: absolute; left: 60px; top: 150px; width: 300px; }
  .brand-name {
    font-weight: 400;
    font-size: 40px;
    color: var(--navy);
    letter-spacing: 3px;
    text-transform: uppercase;
    line-height: 1;
    display: flex;
    align-items: center;
    gap: 12px;
  }
  .brand-square {
    width: 14px; height: 14px;
    background: var(--sky);
    flex: none;
  }
  .brand-tagline {
    margin-top: 12px;
    font-size: 11px;
    letter-spacing: 1px;
    color: var(--tagline-grey);
    text-align: left;
    line-height: 1.35;
  }
  .front-contact { position: absolute; left: 400px; top: 82px; color: var(--text-grey); }
  .person-name { font-size: 28px; font-weight: 400; letter-spacing: 0.5px; text-transform: uppercase; }
  .person-role { font-size: 19px; font-weight: 300; margin-top: 6px; }
  .contact-list { list-style: none; margin-top: 38px; font-size: 18px; font-weight: 300; }
  .contact-list li { display: flex; align-items: center; gap: 12px; margin-bottom: 6px; }
  .contact-list svg { width: 16px; height: 16px; flex: none; }
  .address { margin-top: 40px; font-size: 18px; font-weight: 300; line-height: 1.35; }
  .website { font-size: 18px; font-weight: 700; color: var(--navy-deep); margin-top: 4px; }
  .front-band {
    position: absolute; left: 0; bottom: 0; width: 100%; height: 36px;
    background: linear-gradient(180deg, var(--blue-light) 0%, var(--blue-mid) 30%, var(--blue-dark) 100%);
  }
  /* Back card */
  .card-back {
    top: 500px;
    background: radial-gradient(ellipse at 60% 40%, var(--blue-light) 0%, var(--blue-mid) 45%, var(--blue-dark) 100%);
  }
  .back-brand {
    position: absolute; left: 50%; top: 50%;
    transform: translate(-50%, -50%);
    width: 420px;
  }
  .back-brand .brand-name { font-size: 56px; color: var(--navy-deep); justify-content: center; }
  .back-brand .brand-square { width: 18px; height: 18px; background: var(--navy-deep); }
  .back-brand .brand-tagline { color: var(--tagline-light); font-size: 13px; letter-spacing: 1.4px; margin-top: 14px; text-align: center; }
</style>
</head>
<body>
  <section class="card card-front">
    <div class="front-brand">
      <div class="brand-name"><span class="brand-square"></span>TernVAX</div>
      <p class="brand-tagline">SaaS billing &amp; provisioning software</p>
    </div>
    <div class="front-contact">
      <h1 class="person-name">Dana Marlow</h1>
      <p class="person-role">Director</p>
      <ul class="contact-list">
        <li>
          <svg viewBox="0 0 16 16" aria-hidden="true"><rect x="3" y="1" width="10" height="14" rx="1.5" fill="none" stroke="var(--navy)" stroke-width="1.5"/><line x1="6" y1="12.5" x2="10" y2="12.5" stroke="var(--navy)" stroke-width="1.5"/></svg>
          (954) 555-0142
        </li>
        <li>
          <svg viewBox="0 0 16 16" aria-hidden="true"><rect x="1" y="3" width="14" height="10" fill="none" stroke="var(--navy)" stroke-width="1.5"/><polyline points="1,3 8,9 15,3" fill="none" stroke="var(--navy)" stroke-width="1.5"/></svg>
          dana@ternvax.com
        </li>
      </ul>
      <p class="address">480 NE 9th Street,<br>Harbor Point, FL 33390</p>
      <p class="website">www.ternvax.com</p>
    </div>
    <div class="front-band"></div>
  </section>

  <section class="card card-back">
    <div class="back-brand">
      <div class="brand-name"><span class="brand-square"></span>TernVAX</div>
      <p class="brand-tagline">SaaS billing &amp; provisioning software</p>
    </div>
  </section>
</body>
</html>
```